Law Firm in Texas in need of new letterhead

Law Firm in Fort Worth, TX, USA named "Pell & Varnum, Attorneys-At-Law, LLP." This is a general practice law firm that mostly does Family Law and Criminal Defense work.

We are looking for a new letterhead that has a "classical" appeal, with modern elements.

Any color combination is fine, but please note that we do fax many documents, so the design must be clearly legible in Black and White.

We would like our letterhead to project a sense of professionalism, integrity, and ability.

Target Market(s)

Letterhead will be for correspondence generally with other attorneys and clients.

Industry/Entity Type

Law Firm

Logo Text

Pell & Varnum, Attorneys-At-Law, LLP.

Logo styles of interest
Pictorial/Combination Logo
Wordmark Logo
Lettermark Logo
Requirements
Nice to have
• Although not necessary, a "Texas Star" that is incorporated into the design would be a nice touch.
Should not have
• Colors that do not convert to B&W easily

```html
<!DOCTYPE html>
<html lang="en">
<head>
<meta charset="utf-8">
<title>Pell &amp; Varnum Letterhead</title>
<link rel="stylesheet" href="https://fonts.googleapis.com/css2?family=Cinzel:wght@500&family=Libre+Baskerville:wght@400;700&family=Questrial&family=Montserrat:wght@600&display=swap">
<style>
  :root {
    --backdrop: #c9c9c9;
    --paper: #ffffff;
    --navy: #1f4f82;
    --ink: #3a3a3a;
    --muted: #8a8f96;
    --rule: #9aa6b3;
    --watermark: #eeeeef;
  }
  * { box-sizing: border-box; margin: 0; padding: 0; }
  html, body { width: 1200px; height: 1000px; overflow: hidden; }
  body {
    background: var(--backdrop);
    position: relative;
    font-family: "Questrial", sans-serif;
  }
  .sheet {
    position: absolute;
    top: 150px;
    width: 540px;
    height: 699px;
    background: var(--paper);
    box-shadow: 0 2px 10px rgba(0,0,0,0.12);
  }
  .sheet--blank { left: 40px; }
  .sheet--letter { left: 620px; }

  .masthead {
    position: absolute;
    top: 48px;
    left: 48px;
    display: flex;
    align-items: center;
    gap: 12px;
  }
  .masthead__square {
    width: 14px; height: 14px;
    background: var(--navy);
  }
  .masthead__text { color: var(--navy); font-family: "Cinzel", serif; font-weight: 500; }
  .masthead__name { font-size: 26px; letter-spacing: 1px; line-height: 1; }
  .masthead__tagline { font-size: 10.5px; letter-spacing: 2px; margin-top: 6px; }

  .watermark-star {
    position: absolute;
    top: 175px; left: 110px;
    width: 320px; height: 300px;
    background: radial-gradient(circle at 50% 50%, var(--watermark) 0%, var(--watermark) 45%, rgba(238,238,239,0) 72%);
  }

  .letter-body {
    position: absolute;
    top: 175px; left: 60px; right: 60px;
    font-size: 10.5px;
    line-height: 1.45;
    color: var(--ink);
  }
  .letter-body p { margin-bottom: 12px; }
  .closing { text-align: right; margin-top: 4px; }
  .signature-row {
    position: absolute;
    top: 420px; left: 60px; right: 60px;
    display: flex; align-items: center; justify-content: flex-end; gap: 16px;
  }
  .signature-mark { width: 120px; height: 36px; background: linear-gradient(90deg, #dfe4f3, #c7d0ec); }
  .signer { font-family: "Montserrat", sans-serif; font-weight: 600; font-size: 11px; color: var(--ink); }

  .partners {
    position: absolute;
    top: 510px; right: 40px;
    display: flex;
    font-family: "Libre Baskerville", serif;
    color: var(--muted);
    font-size: 7.5px;
    line-height: 1.55;
  }
  .partner { padding: 0 14px; }
  .partner--first { text-align: right; border-right: 1px solid var(--rule); }
  .partner__name { letter-spacing: 1px; font-size: 8px; margin-bottom: 2px; }
  .partner__web { color: var(--navy); font-weight: 700; margin-top: 6px; }

  .contact {
    position: absolute;
    bottom: 48px; left: 48px;
    display: flex; align-items: center;
    font-family: "Libre Baskerville", serif;
    font-weight: 700;
    font-size: 9px;
    line-height: 1.5;
    color: var(--navy);
  }
  .contact__phones { text-align: right; padding-right: 14px; border-right: 1px solid var(--navy); }
  .contact__address { padding-left: 14px; }
</style>
</head>
<body>

  <section class="sheet sheet--blank">
    <header class="masthead">
      <span class="masthead__square"></span>
      <div class="masthead__text">
        <div class="masthead__name">PELL &amp; VARNUM</div>
        <div class="masthead__tagline">ATTORNEYS AT LAW, LLP</div>
      </div>
    </header>
    <div class="watermark-star" role="img" aria-label="Faint Texas star watermark"></div>
    <div class="partners">
      <div class="partner partner--first">
        <div class="partner__name">ADRIAN PELL</div>
        <div>Managing Partner</div>
        <div>Licensed in the State of Texas</div>
        <div>U.S. District Court</div>
        <div>(Northern District of Texas)</div>
        <div>United States Supreme Court</div>
      </div>
      <div class="partner">
        <div class="partner__name">CLAIRE MARIE VARNUM</div>
        <div>Licensed in the State of Texas</div>
        <div>U.S. District Court</div>
        <div>(Northern District of Texas)</div>
        <div class="partner__web">www.pell-varnum.com</div>
      </div>
    </div>
    <footer class="contact">
      <div class="contact__phones">Phone: (817) 555-0142<br>Fax: (817) 555-0187</div>
      <div class="contact__address">1420 West Magnolia Avenue<br>Fort Worth, Texas 76104</div>
    </footer>
  </section>

  <section class="sheet sheet--letter">
    <header class="masthead">
      <span class="masthead__square"></span>
      <div class="masthead__text">
        <div class="masthead__name">PELL &amp; VARNUM</div>
        <div class="masthead__tagline">ATTORNEYS AT LAW, LLP</div>
      </div>
    </header>
    <div class="letter-body">
      <p>Thank you for meeting with our office last week. We have reviewed the documents you provided and prepared a summary of the next steps in your matter for your review.</p>
      <p>Please gather any remaining records and bring them to your next appointment so we can complete the filing on schedule.</p>
      <p>Should any questions arise before then, our staff will gladly assist you by phone or email during regular office hours.</p>
      <p>We appreciate the trust you have placed in our firm and look forward to working with you.</p>
      <p class="closing">Yours Sincerely,</p>
    </div>
    <div class="signature-row">
      <div class="signature-mark" role="img" aria-label="Handwritten signature"></div>
      <span class="signer">Dana Whitlock</span>
    </div>
    <div class="partners">
      <div class="partner partner--first">
        <div class="partner__name">ADRIAN PELL</div>
        <div>Managing Partner</div>
        <div>Licensed in the State of Texas</div>
        <div>U.S. District Court</div>
        <div>(Northern District of Texas)</div>
        <div>United States Supreme Court</div>
      </div>
      <div class="partner">
        <div class="partner__name">CLAIRE MARIE VARNUM</div>
        <div>Licensed in the State of Texas</div>
        <div>U.S. District Court</div>
        <div>(Northern District of Texas)</div>
        <div class="partner__web">www.pell-varnum.com</div>
      </div>
    </div>
    <footer class="contact">
      <div class="contact__phones">Phone: (817) 555-0142<br>Fax: (817) 555-0187</div>
      <div class="contact__address">1420 West Magnolia Avenue<br>Fort Worth, Texas 76104</div>
    </footer>
  </section>

</body>
</html>
```